Irrigation Business needs their business cards modernised and revamped

I would like to keep my current logo, colours and revamp the format of the card.

I would like the card to be clean yet important.

Im not sure if you include texture but i would like the named logo to be indented into the card etc.

show me something alive and free something thats clinical to the point yet has a feel of achievement. i would like people to go nice card.

Target Market(s)

high end clients, corporate, sports field manger, the guys that make the decisions

Industry/Entity Type

Business

Contact Information for Business Card

nformation to be included

Dean Harlow (Director)
0487305526
dean@kolvat.biz
www.kestonfieldworks.com

instagram logo
google logo
facebook logo

Colors

Designer to choose colors to be used in the design.

Requirements
Nice to have
• indentations a really nice feel to the card good texture

```html
<!DOCTYPE html>
<html lang="en">
<head>
<meta charset="utf-8">
<title>Keston Fieldworks – Business Card</title>
<link href="https://fonts.googleapis.com/css2?family=Roboto:wght@400;500;700;900&display=swap" rel="stylesheet">
<style>
  :root {
    --backdrop: #3b3b3d;
    --card: #222327;
    --card-edge: #2c2d32;
    --brand-blue: #3355a3;
    --sky-blue: #3a9ad9;
    --name-blue: #3d8fd1;
    --emboss: #35373d;
    --emboss-text: #4a4d55;
    --ink: #f2f2f2;
    --muted: #c9cbd0;
    --icon: #5f6f9a;
  }
  * { box-sizing: border-box; margin: 0; padding: 0; }
  html, body { width: 799px; height: 1200px; overflow: hidden; }
  body {
    background: var(--backdrop);
    font-family: "Roboto", Arial, sans-serif;
    position: relative;
  }
  .card {
    position: absolute;
    left: 90px;
    width: 620px;
    height: 354px;
    background: var(--card);
    border: 1px solid var(--card-edge);
    border-radius: 3px;
    overflow: hidden;
  }
  .card--front { top: 120px; }
  .card--back { top: 700px; }

  /* Front */
  .front-mark {
    position: absolute;
    left: 0; right: 0; top: 70px;
    display: flex; flex-direction: column; align-items: center; gap: 18px;
  }
  .front-mark__disc {
    width: 130px; height: 130px; border-radius: 50%;
    background: var(--emboss);
  }
  .front-mark__name {
    color: var(--emboss-text);
    font-weight: 700; font-size: 22px; letter-spacing: 3px;
    text-transform: uppercase;
  }
  .front-social {
    position: absolute; left: 0; right: 0; top: 268px;
    display: flex; align-items: center; justify-content: center; gap: 10px;
  }
  .front-social__rule {
    width: 150px; height: 2px; background: var(--brand-blue);
  }

  .social { display: flex; gap: 7px; }
  .social__dot {
    width: 20px; height: 20px; border-radius: 50%;
    background: var(--brand-blue);
  }

  /* Back */
  .brand {
    position: absolute; left: 30px; top: 30px;
    display: flex; align-items: center; gap: 18px;
  }
  .brand__disc {
    width: 96px; height: 96px; border-radius: 50%;
    background: var(--sky-blue);
    border: 4px solid var(--brand-blue);
  }
  .brand__name {
    color: var(--brand-blue);
    font-weight: 900; font-size: 30px; letter-spacing: 0.5px;
    text-transform: uppercase;
  }
  .person { position: absolute; left: 30px; top: 150px; }
  .person__name {
    color: var(--name-blue); font-weight: 900; font-size: 24px;
    text-transform: uppercase;
  }
  .person__role { color: var(--muted); font-size: 13px; margin-top: 2px; }
  .card--back .social { position: absolute; left: 30px; top: 218px; }

  .contact {
    position: absolute; left: 370px; top: 180px;
    list-style: none; display: flex; flex-direction: column; gap: 5px;
  }
  .contact__item {
    display: flex; align-items: center; gap: 12px;
    color: var(--ink); font-size: 15px;
  }
  .contact__icon { width: 15px; height: 15px; flex: none; }

  .band { position: absolute; left: 0; bottom: 0; width: 620px; height: 110px; }
  .band__url {
    position: absolute; left: 300px; bottom: 24px;
    color: var(--ink); font-size: 16px; font-weight: 500;
  }
</style>
</head>
<body>

<section class="card card--front" aria-label="Card front">
  <div class="front-mark">
    <div class="front-mark__disc"></div>
    <div class="front-mark__name">Keston Fieldworks</div>
  </div>
  <div class="front-social">
    <span class="front-social__rule"></span>
    <div class="social" aria-label="Social media">
      <span class="social__dot"></span><span class="social__dot"></span><span class="social__dot"></span>
    </div>
    <span class="front-social__rule"></span>
  </div>
</section>

<section class="card card--back" aria-label="Card back">
  <div class="brand">
    <div class="brand__disc"></div>
    <div class="brand__name">Keston Fieldworks</div>
  </div>

  <div class="person">
    <div class="person__name">Dean Harlow</div>
    <div class="person__role">Director</div>
  </div>

  <div class="social" aria-label="Social media">
    <span class="social__dot"></span><span class="social__dot"></span><span class="social__dot"></span>
  </div>

  <ul class="contact">
    <li class="contact__item">
      <svg class="contact__icon" viewBox="0 0 16 16" aria-hidden="true"><path fill="var(--icon)" d="M3 1h3l1.5 4-2 1.2a9 9 0 0 0 4.3 4.3L11 8.5l4 1.5v3a2 2 0 0 1-2 2A12 12 0 0 1 1 3a2 2 0 0 1 2-2z"/></svg>
      0487305526
    </li>
    <li class="contact__item">
      <svg class="contact__icon" viewBox="0 0 16 16" aria-hidden="true"><rect x="1" y="3" width="14" height="10" fill="var(--icon)"/><path d="M1 3l7 6 7-6" fill="none" stroke="var(--card)" stroke-width="1.3"/></svg>
      dean@kolvat.biz
    </li>
    <li class="contact__item">
      <svg class="contact__icon" viewBox="0 0 16 16" aria-hidden="true"><g fill="none" stroke="var(--icon)" stroke-width="1.4"><circle cx="8" cy="8" r="6.5"/><ellipse cx="8" cy="8" rx="2.8" ry="6.5"/><path d="M1.5 8h13"/></g></svg>
      www.kestonfieldworks.com
    </li>
  </ul>

  <svg class="band" viewBox="0 0 620 110" aria-hidden="true">
    <polygon points="0,40 270,92 270,110 0,110" fill="var(--sky-blue)"/>
    <polygon points="0,54 270,106 270,110 0,110" fill="var(--sky-blue)"/>
    <polygon points="280,60 620,60 620,110 250,110" fill="var(--brand-blue)"/>
  </svg>
  <div class="band__url">www.kolvat.biz</div>
</section>

</body>
</html>
```